Website Quibrel Outdoor

Hi I'm looking for a simple design for a new website. It's outdoor products mainly in category, Boat, Tarpaulin, Fishing, Golf. I have include image and text for 8 products + presentation etc. I want a simple and modern site + fast + Mobile. Wordpress. I'm going to sell through Tradovik so I don't need any WooCommerce but a buy button to Tradovik. I haven set up the Tradovik account yet. My logo i s grey and orange. My goal is to sell in Tradovik US and later EU.

```html
<!DOCTYPE html>
<html lang="en">
<head>
<meta charset="utf-8">
<title>Quibrel Outdoor</title>
<link href="https://fonts.googleapis.com/css2?family=Archivo+Black&family=Roboto:wght@400;500;700&display=swap" rel="stylesheet">
<style>
:root{
  --orange:#f07c1a;
  --orange-dark:#e46f10;
  --ink:#1f1f1f;
  --text:#555;
  --grey:#8a8a8a;
  --white:#fff;
  --footer:#151515;
  --blog-bg:#2b2f33;
}
*{box-sizing:border-box;margin:0;padding:0}
html,body{width:1200px;height:3856px;overflow:hidden}
body{position:relative;font-family:"Roboto",Arial,sans-serif;color:var(--text);background:var(--white)}
.abs{position:absolute}
.heading{font-family:"Archivo Black","Arial Black",sans-serif;text-transform:uppercase;color:var(--ink);letter-spacing:.5px}
.btn{position:absolute;display:flex;align-items:center;justify-content:center;background:var(--orange);color:var(--white);border-radius:30px;font-weight:700;text-transform:uppercase;font-size:12px;font-family:"Roboto",Arial,sans-serif}
.circle-arrow{position:absolute;width:48px;height:48px;border-radius:50%;display:flex;align-items:center;justify-content:center}

/* hero */
.hero{left:0;top:0;width:1200px;height:685px;background:linear-gradient(100deg,#3d4236 0%,#55584a 35%,#6a5a45 60%,#3a3c33 100%)}
.nav{left:110px;top:52px;display:flex;gap:26px;font-size:14px;font-weight:500;color:var(--white)}
.nav .active{color:var(--orange)}
.brand{left:500px;top:28px;width:200px;text-align:center}
.brand .mark{width:72px;height:56px;border-radius:50%;background:#6f6f6f;margin:0 auto 4px}
.brand .name{font-family:"Roboto",Arial,sans-serif;font-weight:700;color:var(--orange);font-size:34px;line-height:36px;letter-spacing:2px}
.brand .name small{display:block;font-size:22px;letter-spacing:8px;line-height:26px}
.shop{left:746px;top:42px;width:118px;height:36px}
.icons{left:918px;top:52px;display:flex;gap:36px}
.hero-title{left:0;width:1200px;top:322px;text-align:center;color:var(--white);font-size:50px}
.hero-btn{left:540px;top:399px;width:120px;height:36px}
.dots{left:576px;top:607px;display:flex;gap:6px}
.dots span{width:11px;height:11px;border-radius:50%;background:var(--white)}

/* products */
.products{left:0;top:685px;width:1200px;height:368px;background:var(--orange)}
.sec-title{position:absolute;left:0;width:1200px;text-align:center;font-size:32px}
.card-img{position:absolute;top:848px;width:311px;height:205px;background:var(--white)}
.card-img div{position:absolute;left:80px;top:12px;width:151px;height:180px;border-radius:6px}
.prod-text{position:absolute;top:1078px;width:311px;text-align:center}
.prod-text .cat{font-size:11px;color:var(--orange);letter-spacing:.6px;text-transform:uppercase}
.prod-text h3{font-family:"Archivo Black","Arial Black",sans-serif;color:var(--ink);font-size:20px;font-weight:400;margin-top:8px}
.prod-text p{font-size:13px;line-height:21px;margin:8px auto 0;width:270px}
.prod-btn{top:1194px;width:184px;height:45px;font-size:12px}

/* who */
.who-photo{left:124px;top:1342px;width:470px;height:470px;border-radius:50%;background:radial-gradient(circle at 50% 60%,#d9951c 0%,#a06a1c 45%,#3c3d3e 100%)}
.who-title{left:639px;top:1350px;font-size:31px}
.who-text{left:639px;top:1412px;width:450px;font-size:14.5px;line-height:21.4px;color:#5e5e5e}
.who-btn{left:639px;top:1762px;width:118px;height:36px}

/* blog */
.blog{left:0;top:1918px;width:1200px;height:700px;background:linear-gradient(180deg,#4a5058 0%,#2c3036 50%,#23262a 100%)}
.blog-card{position:absolute;top:2073px;width:314px;height:397px;background:var(--white)}
.blog-card .ph{position:absolute;left:12px;top:12px;width:290px;height:184px}
.blog-card h3{position:absolute;left:25px;top:228px;width:270px;font-size:20px;line-height:22px;font-weight:700;color:var(--ink)}
.blog-card .date{position:absolute;left:25px;top:290px;font-size:14px;font-weight:700;color:var(--orange);display:flex;align-items:center;gap:4px}
.blog-card p{position:absolute;left:25px;top:318px;width:250px;font-size:12.3px;line-height:21.5px;color:#666}
.blog-btn{left:507px;top:2500px;width:199px;height:51px;font-size:15px;text-transform:uppercase}

/* gallery */
.g{position:absolute}

/* footer */
.footer{left:0;top:3381px;width:1200px;height:475px;background:var(--footer)}
.f-brand{left:131px;top:3478px;width:180px;text-align:center}
.f-brand .mark{width:76px;height:60px;border-radius:50%;background:#6f6f6f;margin:0 auto 6px}
.social{position:absolute;top:3632px;width:30px;height:30px;border-radius:50%}
.f-col{position:absolute;top:3478px;color:var(--white);font-size:14px}
.f-col h4{font-size:16px;font-weight:700;margin-bottom:21px}
.f-col li{list-style:none;line-height:25.5px}
.contact-item{display:flex;gap:10px;margin-bottom:12px;line-height:17px}
.contact-item b{font-size:12px;display:block}
.f-line{left:112px;top:3705px;width:976px;height:1px;background:#444}
.up{left:1107px;top:3689px;width:36px;height:36px;border-radius:50%;background:var(--orange)}
.copy{left:0;width:1200px;top:3728px;text-align:center;color:var(--white);font-size:14px}
.pay{position:absolute;top:3780px;width:45px;height:27px;border-radius:3px}
</style>
</head>
<body>

<!-- HERO -->
<div class="abs hero" role="img" aria-label="Woman in orange rain jacket fishing in a forest"></div>
<nav class="abs nav"><span class="active">Home</span><span>About us</span><span>Featured</span><span>Blog</span><span>Contact us</span></nav>
<div class="abs brand">
  <div class="mark"></div>
  <div class="name">QUIBREL<small>OUTDOOR</small></div>
</div>
<div class="btn shop">Shop now</div>
<div class="abs icons">
  <svg width="14" height="14" viewBox="0 0 14 14"><circle cx="6" cy="6" r="4.5" fill="none" stroke="#f07c1a" stroke-width="2"/><line x1="9.5" y1="9.5" x2="13" y2="13" stroke="#f07c1a" stroke-width="2"/></svg>
  <svg width="15" height="14" viewBox="0 0 15 14"><path d="M7.5 13 1.5 7A3.4 3.4 0 0 1 7.5 2.5 3.4 3.4 0 0 1 13.5 7Z" fill="#f07c1a"/></svg>
  <svg width="12" height="14" viewBox="0 0 12 14"><circle cx="6" cy="4" r="3.2" fill="#f07c1a"/><path d="M0 14c0-4 2.5-6 6-6s6 2 6 6Z" fill="#f07c1a"/></svg>
  <svg width="15" height="14" viewBox="0 0 15 14"><path d="M0 1h3l2 8h8l2-6H4" fill="none" stroke="#f07c1a" stroke-width="1.8"/><circle cx="6" cy="12" r="1.5" fill="#f07c1a"/><circle cx="12" cy="12" r="1.5" fill="#f07c1a"/></svg>
</div>
<div class="circle-arrow" style="left:28px;top:328px;background:#222"><svg width="10" height="14"><path d="M8 1 2 7l6 6" stroke="#fff" stroke-width="2" fill="none"/></svg></div>
<div class="circle-arrow" style="left:1124px;top:328px;background:#222"><svg width="10" height="14"><path d="m2 1 6 6-6 6" stroke="#fff" stroke-width="2" fill="none"/></svg></div>
<h1 class="abs heading hero-title" style="color:#fff">Quibrel Outdoor</h1>
<div class="btn hero-btn">Learn more</div>
<div class="abs dots"><span></span><span></span><span></span></div>

<!-- PRODUCTS -->
<div class="abs products"></div>
<h2 class="heading sec-title" style="top:778px;color:#fff">Our Product</h2>
<div class="circle-arrow" style="left:28px;top:930px"><svg width="14" height="22"><path d="M12 2 3 11l9 9" stroke="#fff" stroke-width="3" fill="none"/></svg></div>
<div class="circle-arrow" style="left:1124px;top:930px"><svg width="14" height="22"><path d="m2 2 9 9-9 9" stroke="#fff" stroke-width="3" fill="none"/></svg></div>

<div class="card-img" style="left:112px"><div role="img" aria-label="Sunglasses on a lanyard" style="background:linear-gradient(180deg,#ececec,#d7d7dc)"></div></div>
<div class="card-img" style="left:444px"><div role="img" aria-label="Tarpaulin shelter with tent hooks" style="left:40px;width:231px;background:linear-gradient(180deg,#f0f0f0,#dadada)"></div></div>
<div class="card-img" style="left:776px"><div role="img" aria-label="Grey towel with orange clip" style="background:linear-gradient(180deg,#e9e9e9,#9a9a9a)"></div></div>

<div class="prod-text" style="left:112px"><div class="cat">Duis aute irure</div><h3>Duis aute irure dolor</h3><p>Lorem ipsum dolor sit amet, consectetur adipiscing elit, sed do</p></div>
<div class="prod-text" style="left:444px"><div class="cat">Duis aute irure</div><h3>Duis aute irure dolor</h3><p>Lorem ipsum dolor sit amet, consectetur adipiscing elit, sed do</p></div>
<div class="prod-text" style="left:776px"><div class="cat">Duis aute irure</div><h3>Duis aute irure dolor</h3><p>Lorem ipsum dolor sit amet, consectetur adipiscing elit, sed do</p></div>
<div class="btn prod-btn" style="left:175px">Buy on Tradovik</div>
<div class="btn prod-btn" style="left:508px">Buy on Tradovik</div>
<div class="btn prod-btn" style="left:840px">Buy on Tradovik</div>

<!-- WHO WE ARE -->
<div class="abs who-photo" role="img" aria-label="Woman stepping onto a yellow motor boat at a marina"></div>
<h2 class="abs heading who-title">Who we are</h2>
<p class="abs who-text">Lorem ipsum dolor sit amet, consectetur adipiscing elit, sed do eiusmod tempor incididunt ut labore et dolore magna aliqua. Ut enim ad minim veniam, quis nostrud exercitation ullamco laboris nisi ut aliquip ex ea commodo consequat. Duis aute irure dolor in reprehenderit in voluptate velit esse cillum dolore eu fugiat nulla pariatur. Excepteur sint occaecat cupidatat non proident, sunt in culpa qui officia deserunt mollit anim id est laborum. Lorem ipsum dolor sit amet, consectetur adipiscing elit, sed do eiusmod tempor incididunt ut labore et dolore magna aliqua. Ut enim ad minim veniam, quis nostrud exercitation ullamco laboris nisi ut aliquip ex ea commodo consequat. Duis aute irure dolor in reprehenderit in voluptate velit esse cillum dolore eu fugiat nulla pariatur. Excepteur sint occaecat cupidatat non proident, sunt in culpa qui officia deserunt mollit anim id est laborum.</p>
<div class="btn who-btn">Learn more</div>

<!-- BLOG -->
<div class="abs blog" role="img" aria-label="Boats under covers in a dim harbour"></div>
<h2 class="heading sec-title" style="top:2000px;color:#fff">Latest Blog</h2>
<div class="circle-arrow" style="left:28px;top:2288px;background:#bbb;opacity:.8"><svg width="10" height="14"><path d="M8 1 2 7l6 6" stroke="#555" stroke-width="1.5" fill="none"/></svg></div>
<div class="circle-arrow" style="left:1124px;top:2288px;background:#bbb;opacity:.8"><svg width="10" height="14"><path d="m2 1 6 6-6 6" stroke="#555" stroke-width="1.5" fill="none"/></svg></div>

<div class="blog-card" style="left:105px">
  <div class="ph" role="img" aria-label="Golf bag on a trolley with a glove" style="background:linear-gradient(135deg,#6f7a5a,#a9a9a3)"></div>
  <h3>Lorem ipsum dolor sit amet, consectetur</h3>
  <div class="date"><svg width="12" height="12"><rect x="1" y="2" width="10" height="9" fill="#f07c1a"/></svg>Dec 6, 2021</div>
  <p>Lorem ipsum dolor sit amet, consectetur adipiscing elit, sed do eiusmod tempor incididunt ut labore et dolore</p>
</div>
<div class="blog-card" style="left:443px">
  <div class="ph" role="img" aria-label="Tent poles and ropes on a deck" style="background:linear-gradient(135deg,#3b3d3f,#8c8d8c)"></div>
  <h3>Lorem ipsum dolor sit amet, consectetur</h3>
  <div class="date"><svg width="12" height="12"><rect x="1" y="2" width="10" height="9" fill="#f07c1a"/></svg>Dec 1, 2021</div>
  <p>Lorem ipsum dolor sit amet, consectetur adipiscing elit, sed do eiusmod tempor incididunt ut labore et dolore</p>
</div>
<div class="blog-card" style="left:781px">
  <div class="ph" role="img" aria-label="White boat hull with a green sticker" style="background:linear-gradient(180deg,#5e6670,#e4e6e8)"></div>
  <h3>Lorem ipsum dolor sit amet, consectetur</h3>
  <div class="date"><svg width="12" height="12"><rect x="1" y="2" width="10" height="9" fill="#f07c1a"/></svg>Nov 1, 2021</div>
  <p>Lorem ipsum dolor sit amet, consectetur adipiscing elit, sed do eiusmod tempor incididunt ut labore et dolore</p>
</div>
<div class="btn blog-btn">View more blogs</div>

<!-- GALLERY -->
<h2 class="heading sec-title" style="top:2712px">Gallery</h2>
<div class="g" style="left:111px;top:2778px;width:317px;height:242px;background:linear-gradient(135deg,#5f8a3a,#6f6d6a)" role="img" aria-label="Golf bag on a trolley on grass"></div>
<div class="g" style="left:441px;top:2778px;width:317px;height:500px;background:linear-gradient(180deg,#6d7a3c,#b8652a 55%,#2f3340)" role="img" aria-label="Woman in orange jacket holding a fishing rod"></div>
<div class="g" style="left:772px;top:2778px;width:317px;height:242px;background:linear-gradient(135deg,#3a3b3d,#7b9a4a)" role="img" aria-label="Towel clipped to a golf bag"></div>
<div class="g" style="left:111px;top:3035px;width:317px;height:243px;background:linear-gradient(135deg,#5c8a38,#c9c9c9 50%,#4a4340)" role="img" aria-label="Golfer wiping a glove with a towel"></div>
<div class="g" style="left:772px;top:3035px;width:317px;height:243px;background:linear-gradient(180deg,#9a7d78,#7a6a68 60%,#4a4546)" role="img" aria-label="Fisherman at sunset by the water"></div>

<!-- FOOTER -->
<div class="abs footer"></div>
<div class="abs f-brand">
  <div class="mark"></div>
  <div style="font-weight:700;color:var(--orange);font-size:42px;line-height:42px;letter-spacing:2px">QUIBREL</div>
  <div style="font-weight:700;color:var(--orange);font-size:26px;line-height:30px;letter-spacing:9px">OUTDOOR</div>
</div>
<div class="social" style="left:141px;background:#3b5998"></div>
<div class="social" style="left:179px;background:#1da1f2"></div>
<div class="social" style="left:218px;background:#dd4b39"></div>
<div class="social" style="left:257px;background:#b8318f"></div>

<div class="f-col" style="left:446px"><h4>Quick Links</h4><ul><li>Home</li><li>About us</li><li>Products</li><li>Testimonials</li><li>Contact</li></ul></div>
<div class="f-col" style="left:640px"><h4>About Company</h4><ul><li>Pricing</li><li>Free Demo</li><li>Resources</li><li>Contact</li><li>Login</li></ul></div>
<div class="f-col" style="left:871px;width:230px"><h4>Contact Us</h4>
  <div class="contact-item"><svg width="13" height="13" viewBox="0 0 13 13"><path d="M2 1l3 0 1 3-2 1.5a8 8 0 0 0 3.5 3.5L9 7l3 1v3c0 1-1 1-1 1A11 11 0 0 1 1 2s0-1 1-1Z" fill="#f07c1a"/></svg><div><b>Phone</b>+888 888 8888</div></div>
  <div class="contact-item"><svg width="14" height="11" viewBox="0 0 14 11"><rect width="14" height="11" fill="#f07c1a"/><path d="M0 0l7 6 7-6" stroke="#151515" fill="none"/></svg><div><b>Email</b>info@companyname.com</div></div>
  <div class="contact-item"><svg width="12" height="15" viewBox="0 0 12 15"><path d="M6 15S0 8.5 0 5.5a6 6 0 0 1 12 0C12 8.5 6 15 6 15Z" fill="#f07c1a"/><circle cx="6" cy="5.5" r="2" fill="#151515"/></svg><div><b>Location</b>Lorem ipsum dolor sit amet, con elit, sed</div></div>
</div>
<div class="abs f-line"></div>
<div class="abs up" style="display:flex;align-items:center;justify-content:center"><svg width="14" height="10"><path d="M1 8l6-6 6 6" stroke="#fff" stroke-width="2" fill="none"/></svg></div>
<div class="abs copy">2021 Copyright - Company name| All Rights Reserved</div>
<div class="pay" style="left:427px;background:#e8e8ec"></div>
<div class="pay" style="left:487px;background:#e0e0e0"></div>
<div class="pay" style="left:547px;background:#2a6cb4"></div>
<div class="pay" style="left:607px;background:#e6e9f2"></div>
<div class="pay" style="left:667px;background:#3a3f8c"></div>
<div class="pay" style="left:727px;background:#2a2a2a"></div>

</body>
</html>
```